Web Design job: SaaS start-up needs a cutting-edge web design

What's Needed:
- All designs files created
- Fully coded implementation in HTML/CSS/Bootstrap
- Pages: 5 -- see content here http://www.TeamVerdexa.com
-- Home Page
-- The Hidden Value
-- Benefits
-- About us
-- Careers
- The existing site has the textual content for each page. We can tweak to meet specific designs if needed.
- You will need to update/create image and interactive content for pages.

Reference:
Our existing website has a lot of content on it for reference -
http://www.TeamVerdexa.com

Description:
We need a web design that focuses in the UX and conveys the idea of magically fixing company problems by way of using our software.

Home Page
The main goal is to Drive Sales of the SaaS tool. When a visitor lands on our home page they should see: What we do, How we can help their problem and How to contact us.
1. Quickly understand What We Do
-- we sell SaaS software.
-- Need to quickly convey what our software does. It's seems complicated but really its not. See the description in about us for more info and visit our existing site.

2. How we can help their problem
-- We aim to solve any problem related to employees
-- Even if the visitor does not have a specific problem in mind, there are several areas organizations can always improve: (some examples below)
---- Create Stronger, More Productive Teams
---- Build Better Communications Pathways
---- Encourage Innovation and Positive Change
---- Develop and Retain Strong "Company Culture"

3. Be able to Contact Us to get started
-- contacting us to get a sales lead is the ultimate goal.
-- the user should not have to hunt to contact us. needs to be easy.

Other Pages (Hidden Value, Benefit, About Us, Careers):
-- These are informative pages about our software and process.
-- If we grab the attention of the user on the home page then these are the pages that they will explore for more info.
-- Should be able to link to these pages from the main nav or from sections with the homepage. For example: What We Do sections could link to the benefits page. How we help their problem sections could link to the Hidden Value page. Regardless of what links to where, the idea is that we will be able to nav to other areas.

About Us:
Our company name is TeamVerdexa (as in Organizational Analysis). We provide a software as a service (SaaS) that uses a simple 6-question survey to analyze the relationships of people within an Organization and provide leaders with ground-breaking Insights about their teams, interactive social network data visualizations to explore their team's composition and we give detailed profiles of the key players (i.e, who are the Social Bridges, Who are the Knowledge Bottlenecks, Who are the Best Mentors, Who are the people that are completely disconnected/out of the loop). Leaders then use this information to make high level organizational decisions.

What's unique about our software:
-- Powerful analysis results from just a 6-question "pulse-surveys"
-- Innovative Tools for visually exploring the organization through relationships as opposed to org-chart
-- Get real-time results as opposed to waiting months with traditional methods
-- Traditional Org-charts represent the organization's skeleton, whereas we uncover the organization's neural network (how it solves problems).

Preferred fonts (but could be convinced otherwise if looks great):
-- Section titles - Aleo
-- Main body - Lato
-- TeamVerdexa logo - Philosopher

Things we like:
-- We like a big slider as the top of the landing page.

Colors to include:
-- Colors in the logo (red, blue, green, teal) as accent colors

Feel of the site:
-- Cutting-edge Software
-- Professional
-- Social Network flare (we analyze relationships)

Note:
If we find a great match with a designer there is strong possibility to continue the relationship with follow on work redesigning our web-based application.

Target Market(s)

Current customers are Morrow Pike & Fenwell, Clearbrook Valley Bank.
We target anyone that manages a large team. Such as Corporate Leaders, High Level Managers, HR Leaders

Industry/Entity Type

Business Software

Contact Information for Business Card

Logo image
Name of company "TEAMVERDEXA" In Philosopher font.
Tagline: "Unlock the Hidden Value In Your Teams"
Person's Name, Title, email, phone.

Coding

Coded - Design and coding required

Number of Pages Required

4 page

Font styles to use
Other font styles liked:
• Lato, Philosopher, Aero

Colors
ec1f27
0255a3

Requirements
Must have
• See description.
Nice to have
• Things we like:
• We like a big slider as the top of the landing page. Ours is a little clunky and outdated but something fresh and sleek would be great.
• Colors to include:
• We would like to use the colors in the logo as accent colors in the site to give a consistent look and feel.
• Feel of the site:
• Cutting-edge Software
• Professional
• Social Network flare (we analyze relationships)

```html
<!DOCTYPE html>
<html lang="en">
<head>
<meta charset="utf-8">
<title>TeamVerdexa — Home</title>
<link href="https://fonts.googleapis.com/css2?family=Aleo:wght@400;700&family=Lato:wght@400;700&display=swap" rel="stylesheet">
<style>
:root{
  --red:#e3141d;
  --navy:#2b3a8c;
  --icon:#1e3266;
  --green:#178a2c;
  --btn-green:#1b8f2a;
  --blue:#1da1f2;
  --ink:#222;
  --muted:#777;
  --line:#e3e3e3;
  --soft:#f7f7f7;
}
*{box-sizing:border-box;margin:0;padding:0}
html,body{width:1200px;height:4063px;overflow:hidden}
body{font-family:"Lato",sans-serif;color:var(--ink);background:#fff;position:relative}
.abs{position:absolute}
h1,h2,h3{font-family:"Aleo",serif;font-weight:400}

/* header */
.site-header{left:0;top:0;width:1200px;height:108px;background:#fff}
.brand{left:200px;top:24px;display:flex;align-items:center;gap:10px}
.brand-mark{width:22px;height:22px;border-radius:50%;background:var(--red)}
.brand-name{font-family:"Lato",sans-serif;font-weight:700;font-size:17px;color:var(--navy);letter-spacing:1px}
.main-nav{left:460px;top:48px;display:flex;gap:34px;align-items:center;font-size:12px;font-weight:700;text-transform:uppercase;color:#333}
.main-nav .active{color:#333;border-bottom:3px solid var(--red);padding-bottom:12px;margin-bottom:-15px}
.client-login{background:var(--btn-green);color:#fff;padding:9px 16px;border-radius:2px}

/* hero */
.hero{left:0;top:108px;width:1200px;height:532px;background:linear-gradient(90deg,#b7b9bd 0%,#8f9aa6 45%,#6d7d8e 100%)}
.hero-title{left:0;top:218px;width:1200px;text-align:center;color:#fff;font-size:56px}
.hero-sub{left:0;top:296px;width:1200px;text-align:center;color:#eef;font-size:19px}
.dots{left:563px;top:486px;display:flex;gap:12px}
.dots span{width:10px;height:10px;border-radius:50%;background:#fff}
.dots span:first-child{background:var(--red)}

/* about */
.network-art{left:108px;top:690px;width:420px;height:420px;border-radius:50%;background:radial-gradient(circle,#c9a6e8 0%,#b3c2f0 45%,#fff 72%)}
.about-title{left:575px;top:760px;font-size:40px;color:#333}
.about-text{left:575px;top:842px;width:370px;font-size:13px;line-height:22px;color:#555}
.btn-red{background:var(--red);color:#fff;font-size:11px;font-weight:700;text-transform:uppercase;display:inline-block;text-align:center;line-height:30px;width:108px;height:30px}
.about-btn{left:575px;top:1032px}
.divider{left:0;top:1173px;width:1200px;height:1px;background:var(--line)}

/* what we do */
.what{left:0;top:1174px;width:1200px;height:1341px;background:var(--soft)}
.what-title{left:0;top:1245px;width:1200px;text-align:center;font-size:40px;color:#333}
.service{width:400px}
.service h3{font-size:19px;color:var(--navy);margin-bottom:28px}
.service p{font-size:13px;line-height:22px;color:#777;margin-bottom:32px}
.icon-circle{width:210px;height:210px;border-radius:50%;background:#fff;box-shadow:0 8px 14px rgba(0,0,0,.18);display:flex;align-items:center;justify-content:center}

/* help */
.help-left{left:0;top:2515px;width:640px;height:534px;background:var(--green);color:#fff}
.help-right{left:640px;top:2515px;width:560px;height:534px;background:#fff}
.help-title{left:240px;top:2625px;width:360px;font-size:36px;line-height:42px;color:#fff}
.help-sub{left:240px;top:2720px;font-size:13px;color:#fff}
.help-rule{left:240px;top:2762px;width:357px;height:2px;background:#fff}
.help-text{left:240px;top:2785px;width:380px;font-size:27px;line-height:36px;color:#fff}
.benefit{left:693px;display:flex;align-items:center;gap:24px;width:360px}
.benefit .ic{width:70px;height:70px;border-radius:50%;border:1px solid #cfd8e3;box-shadow:0 2px 5px rgba(0,0,0,.12);display:flex;align-items:center;justify-content:center;flex:none}
.benefit span{font-size:17px;line-height:25px;color:#333}

/* contact */
.contact-title{left:0;top:3118px;width:1200px;text-align:center;font-size:38px;color:#333}
.map{left:271px;top:3190px;width:659px;height:292px;background:linear-gradient(135deg,#e6e2d4 0%,#d8dccb 50%,#c9d6e4 100%);border:3px solid #ddd}
.message-title{left:0;top:3515px;width:1200px;text-align:center;font-size:36px;color:#333}
.field{background:#fff;border:1px solid #e4e4e4;font-size:11px;color:#999;padding:12px 14px}
.send{left:550px;top:3742px;width:100px;height:36px;background:var(--blue);color:#fff;font-size:13px;font-weight:700;text-align:center;line-height:36px}

/* footer */
.footer-rule{left:0;top:3835px;width:1200px;height:1px;background:var(--line)}
.foot-brand{left:0;top:3930px;width:1200px;display:flex;justify-content:center;align-items:center;gap:10px}
.foot-links{left:0;top:3978px;width:1200px;text-align:center;font-size:14px;color:#333;word-spacing:4px}
.copyright{left:0;top:4012px;width:1200px;text-align:center;font-size:13px;font-weight:700;color:#333}
</style>
</head>
<body>

<header class="abs site-header">
  <div class="abs brand"><span class="brand-mark"></span><span class="brand-name">TEAMVERDEXA</span></div>
  <nav class="abs main-nav">
    <span class="active">Home</span><span>The Hidden Value</span><span>Benefits</span><span>About Us</span><span>Careers</span>
    <span class="client-login">Client Login</span>
  </nav>
</header>

<section class="abs hero" role="img" aria-label="Slider photo: business person touching a connected network of icons over a world map"></section>
<h1 class="abs hero-title">Team Verdexa</h1>
<p class="abs hero-sub">Sed ut perspiciatis unde omnis iste natus error sit voluptatem</p>
<div class="abs dots"><span></span><span></span><span></span><span></span></div>

<div class="abs network-art" role="img" aria-label="Colourful social network graph of connected nodes"></div>
<h2 class="abs about-title">About Us</h2>
<p class="abs about-text">Our company name is TeamVerdexa (as in Organizational Analysis). We provide a software as a service (SaaS) that uses a simple 6-question survey to analyze the relationship of people within an Organization and provide leaders with ground-breaking Insights about their teams, interactive social network data visualizations to explore their team's composition and we give detailed profiles of the key players.</p>
<a class="abs btn-red about-btn">Learn More</a>
<div class="abs divider"></div>

<section class="abs what"></section>
<h2 class="abs what-title">What We Do ?</h2>

<div class="abs service" style="left:200px;top:1405px">
  <h3>On-Line Survey</h3>
  <p>Sed ut perspiciatis unde omnis iste natus error sit voluptatem accusantium doloremque laudantium, totam rem aperiam, eaque ipsa quae ab illo inventore veritatis et quasi architecto beatae vitae dicta sunt explicabo.</p>
  <a class="btn-red">Learn More</a>
</div>
<div class="abs icon-circle" style="left:690px;top:1376px">
  <svg width="90" height="100" viewBox="0 0 90 100" fill="none" stroke="var(--icon)" stroke-width="6" stroke-linejoin="round"><rect x="8" y="10" width="74" height="86" rx="8"/><rect x="30" y="3" width="30" height="14" rx="3"/><path d="M20 40l6 6 10-12M20 66l6 6 10-12M46 42h24M46 68h24"/></svg>
</div>

<div class="abs icon-circle" style="left:302px;top:1658px">
  <svg width="90" height="100" viewBox="0 0 90 100" fill="none" stroke="var(--icon)" stroke-width="6" stroke-linejoin="round"><path d="M30 6l7 14 15 2-11 10 3 15-14-8-14 8 3-15L8 22l15-2z"/><path d="M42 96V56a6 6 0 0 1 12 0v20l18 4a8 8 0 0 1 6 9l-2 7"/></svg>
</div>
<div class="abs service" style="left:610px;top:1688px">
  <h3>Expert Review &amp; Action Plus</h3>
  <p>Sed ut perspiciatis unde omnis iste natus error sit voluptatem accusantium doloremque laudantium, totam rem aperiam, eaque ipsa quae ab illo inventore veritatis et quasi architecto beatae vitae dicta sunt explicabo.</p>
  <a class="btn-red">Learn More</a>
</div>

<div class="abs service" style="left:200px;top:1937px">
  <h3>Propriatry Algorithms</h3>
  <p>Sed ut perspiciatis unde omnis iste natus error sit voluptatem accusantium doloremque laudantium, totam rem aperiam, eaque ipsa quae ab illo inventore veritatis et quasi architecto beatae vitae dicta sunt explicabo.</p>
  <a class="btn-red">Learn More</a>
</div>
<div class="abs icon-circle" style="left:690px;top:1938px">
  <svg width="100" height="100" viewBox="0 0 100 100" fill="none" stroke="var(--icon)" stroke-width="6" stroke-linecap="round"><circle cx="58" cy="42" r="32"/><path d="M34 66L8 92"/><path d="M44 54V44M56 54V34M68 54V40"/></svg>
</div>

<div class="abs icon-circle" style="left:302px;top:2198px">
  <svg width="100" height="100" viewBox="0 0 100 100" fill="none" stroke="var(--icon)" stroke-width="6"><circle cx="50" cy="50" r="32"/><path d="M30 40c10 6 18 0 24 8s-4 14 4 22M60 22c-6 8 4 12 12 14"/><circle cx="14" cy="30" r="6" fill="var(--icon)"/><circle cx="86" cy="70" r="6" fill="var(--icon)"/></svg>
</div>
<div class="abs service" style="left:610px;top:2191px">
  <h3>Organizational Key Insights</h3>
  <p>Sed ut perspiciatis unde omnis iste natus error sit voluptatem accusantium doloremque laudantium, totam rem aperiam, eaque ipsa quae ab illo inventore veritatis et quasi architecto beatae vitae dicta sunt explicabo.</p>
  <a class="btn-red">Learn More</a>
</div>

<section class="abs help-left"></section>
<section class="abs help-right"></section>
<h2 class="abs help-title">How We Can Help Their Problem</h2>
<p class="abs help-sub">We aim to solve any problem related to employees</p>
<div class="abs help-rule"></div>
<p class="abs help-text">Even if the visitor does not have a specific problem in mind, there are several areas organizations can always improve</p>

<div class="abs benefit" style="top:2597px"><span class="ic"><svg width="34" height="34" viewBox="0 0 34 34" fill="none" stroke="var(--blue)" stroke-width="2.5"><circle cx="17" cy="10" r="5"/><circle cx="7" cy="20" r="4"/><circle cx="27" cy="20" r="4"/><path d="M9 32c0-6 4-10 8-10s8 4 8 10"/></svg></span><span>Create Stronger, More Productive Teams</span></div>
<div class="abs benefit" style="top:2702px"><span class="ic"><svg width="34" height="34" viewBox="0 0 34 34" fill="none" stroke="var(--blue)" stroke-width="2.5"><circle cx="17" cy="9" r="6"/><circle cx="6" cy="27" r="4"/><circle cx="17" cy="27" r="4"/><circle cx="28" cy="27" r="4"/><path d="M17 15v8M6 23l8-8M28 23l-8-8"/></svg></span><span>Build Better Communications Pathways</span></div>
<div class="abs benefit" style="top:2810px"><span class="ic"><svg width="34" height="34" viewBox="0 0 34 34" fill="none" stroke="var(--blue)" stroke-width="2.5"><path d="M17 4a9 9 0 0 1 5 16v4h-10v-4A9 9 0 0 1 17 4z"/><path d="M13 28h8M15 32h4"/></svg></span><span>Encourage Innovation &amp; Positive Change</span></div>
<div class="abs benefit" style="top:2911px"><span class="ic"><svg width="34" height="34" viewBox="0 0 34 34" fill="none" stroke="var(--blue)" stroke-width="2.5"><rect x="3" y="6" width="28" height="20" rx="2"/><path d="M12 32h10M17 26v6M10 20l6-6 4 4 5-6"/></svg></span><span>Develop and Retain Strong "Company Culture"</span></div>

<h2 class="abs contact-title">Contact Us To Get Started</h2>
<div class="abs map" role="img" aria-label="City street map showing the office location"></div>

<h2 class="abs message-title">Send Us A Message</h2>
<div class="abs field" style="left:271px;top:3607px;width:320px;height:40px">Name</div>
<div class="abs field" style="left:271px;top:3670px;width:320px;height:40px">E-mail</div>
<div class="abs field" style="left:609px;top:3607px;width:321px;height:110px">Message (Optional)</div>
<div class="abs send">SEND</div>

<div class="abs footer-rule"></div>
<div class="abs foot-brand"><span class="brand-mark"></span><span class="brand-name">TEAMVERDEXA</span></div>
<p class="abs foot-links">Home &nbsp;|&nbsp; The Hidden Value &nbsp;|&nbsp; About Us</p>
<p class="abs copyright">© 2016 TeamVerdexa. All Rights Reserved.</p>

</body>
</html>
```